GTP biz card

We need a business card design for our new company based in Los Angeles called "Gold Tide Pictures". We develop film and television projects. We work with investors, financiers, film production companies, film distribution and sales companies as well as studios. We would like to incorporate our logo (see attached) on a two-sided card. We need to include: name and title, address, phone, email and company website.

Target Market(s)

Business, financial and studio clients

Industry/Entity Type

Business

Contact Information for Business Card

Two-sided. We are thinking of the logo on one side and the information on the back. Please feel free to be creative! Thanks.

Requirements
Must have
• Please include the following text information, excluding the "CAPS CATEGORY:" and please allow the ability for us to change the name, title and email address for each company employee):
• NAME & TITLE:
• Neil Parker
• Managing Partner
• COMPANY NAME:
• GOLD TIDE PICTURES (please use existing logo)
• COMPANY ADDRESS:
• KTW Studio Park
• 2250 Halverd Street
• Harbor Wing, 4th Floor
• Manhattan Beach, CA 90412
• COMPANY PHONE NUMBER:
• 310-555-0148
• COMPANY WEBSITE ADDRESS:
• www.goldtidepicturesgroup.example
• EMAIL ADDRESS: (only one per card)
• peter@goldtidepicturesgroup.example
• bingo@goldtidepicturesgroup.example
• neil@goldtidepicturesgroup.example

```html
<!DOCTYPE html>
<html lang="en">
<head>
<meta charset="utf-8">
<title>Gold Tide Pictures — Business Card</title>
<link rel="stylesheet" href="https://fonts.googleapis.com/css2?family=Lato:wght@400;700;900&family=Montserrat:wght@500;700&display=swap">
<style>
  :root {
    --stage: #2a2522;
    --card: #050505;
    --band: #16a6ef;
    --bar-light: #bfe9f7;
    --bar-mid: #7fd0ec;
    --ink-dark: #0b1a22;
    --logo-blue: #2fa8e0;
    --glow: #1b6f9a;
    --white: #ffffff;
  }
  * { box-sizing: border-box; margin: 0; padding: 0; }
  html, body { width: 1200px; height: 678px; overflow: hidden; }
  body { background: var(--stage); position: relative; font-family: "Lato", sans-serif; }

  .card { position: absolute; background: var(--card); overflow: hidden; box-shadow: 0 10px 30px rgba(0,0,0,.5); }

  /* Information side (portrait) */
  .card--info { left: 120px; top: 64px; width: 320px; height: 550px; }
  .card--info .band { position: absolute; left: 0; right: 0; height: 14px; background: var(--band); }
  .card--info .band--top { top: 0; }
  .card--info .band--bottom { bottom: 0; }

  .name-tag {
    position: absolute; left: 120px; top: 36px; width: 176px; height: 52px;
    background: linear-gradient(90deg, var(--bar-mid), var(--bar-light));
    padding: 7px 12px; color: var(--ink-dark);
  }
  .name-tag .person { font-family: "Montserrat", sans-serif; font-weight: 700; font-size: 17px; line-height: 1.1; white-space: nowrap; }
  .name-tag .role { font-size: 12px; font-weight: 700; }

  .brand { position: absolute; left: 0; right: 0; text-align: center; }
  .brand .disc {
    display: block; margin: 0 auto; border-radius: 50%;
    background: radial-gradient(circle, var(--glow) 0%, #0a2b3d 55%, var(--card) 75%);
  }
  .brand .company { font-family: "Lato", sans-serif; font-weight: 900; color: var(--logo-blue); letter-spacing: .08em; white-space: nowrap; }
  .brand .tagline { font-family: "Montserrat", sans-serif; font-weight: 500; color: var(--white); letter-spacing: .12em; white-space: nowrap; }

  .card--info .brand { top: 106px; }
  .card--info .brand .disc { width: 100px; height: 100px; }
  .card--info .brand .company { font-size: 19px; margin-top: 12px; }
  .card--info .brand .tagline { font-size: 8.5px; margin-top: 6px; }

  .contacts { position: absolute; left: 26px; right: 26px; top: 292px; list-style: none; }
  .contacts li {
    display: flex; align-items: center; gap: 12px; min-height: 38px; margin-bottom: 9px;
    padding: 6px 8px; background: linear-gradient(90deg, var(--bar-mid), var(--bar-light));
    color: var(--ink-dark); font-size: 12.5px; font-weight: 700; white-space: nowrap;
  }
  .contacts .address { font-size: 11.5px; line-height: 1.35; }
  .contacts svg { width: 20px; height: 20px; flex: none; }

  /* Logo side (landscape) */
  .card--logo { left: 520px; top: 170px; width: 600px; height: 340px; }
  .card--logo .band { position: absolute; top: 0; bottom: 0; width: 22px; background: var(--band); }
  .card--logo .band--left { left: 10px; }
  .card--logo .band--right { right: 10px; }
  .card--logo .brand { top: 58px; }
  .card--logo .brand .disc { width: 130px; height: 130px; }
  .card--logo .brand .company { font-size: 30px; margin-top: 18px; }
  .card--logo .brand .tagline { font-size: 11px; margin-top: 10px; }
</style>
</head>
<body>
  <section class="card card--info" aria-label="Business card, information side">
    <div class="band band--top"></div>
    <div class="name-tag">
      <p class="person">NEIL PARKER</p>
      <p class="role">Managing Partner</p>
    </div>
    <div class="brand">
      <span class="disc"></span>
      <p class="company">GOLD TIDE PICTURES</p>
      <p class="tagline">A MEDIA ENTERTAINMENT COMPANY</p>
    </div>
    <ul class="contacts">
      <li>
        <svg viewBox="0 0 20 20"><rect x="5" y="2" width="10" height="16" rx="2" fill="var(--white)"/><rect x="7" y="4" width="6" height="10" fill="var(--bar-mid)"/></svg>
        310-555-0148
      </li>
      <li>
        <svg viewBox="0 0 20 20"><rect x="2" y="5" width="16" height="11" fill="var(--white)"/><path d="M2 5l8 6 8-6" fill="none" stroke="var(--bar-mid)" stroke-width="1.5"/></svg>
        neil@goldtidepicturesgroup.example
      </li>
      <li>
        <svg viewBox="0 0 20 20"><circle cx="10" cy="10" r="7.5" fill="var(--white)"/><ellipse cx="10" cy="10" rx="3" ry="7.5" fill="none" stroke="var(--bar-mid)" stroke-width="1.3"/><path d="M2.5 10h15" stroke="var(--bar-mid)" stroke-width="1.3"/></svg>
        www.goldtidepicturesgroup.example
      </li>
      <li class="address">
        <svg viewBox="0 0 20 20"><path d="M10 18s-6-6.5-6-10.5a6 6 0 0 1 12 0C16 11.5 10 18 10 18z" fill="var(--white)"/><circle cx="10" cy="7.5" r="2.2" fill="var(--bar-mid)"/></svg>
        <span>KTW Studio Park, 2250 Halverd Street<br>Harbor Wing, 4th Floor<br>Manhattan Beach, CA 90412</span>
      </li>
    </ul>
    <div class="band band--bottom"></div>
  </section>

  <section class="card card--logo" aria-label="Business card, logo side">
    <div class="band band--left"></div>
    <div class="brand">
      <span class="disc"></span>
      <p class="company">GOLD TIDE PICTURES</p>
      <p class="tagline">A MEDIA ENTERTAINMENT COMPANY</p>
    </div>
    <div class="band band--right"></div>
  </section>
</body>
</html>
```